Web Design

We need a website for a company based in Doha Qatar called
Lumara Maid Service.

It is the number one maid cleaning service company, and we have branches all over qatar.

Luxury Cleaning Service Provider.

The color scheme is gold, yellow and black like the logo.

Before they get to the website, there is an intro video.

The website should depict luxury.

Target Market(s)

People who need maids at their houses.

Industry/Entity Type

Cleaning Service

Requirements
Must have
• Luxury, Sleek, Modern

The opening sequence is a video which I already have. Its too big to upload here so I am going to put it on youtube.

After the opening sequence, the home page should have a widescreen photo background and it should change every five seconds, the first background photo should be of qatar westbay skyline. Then the second background should be of maid photos in cleaning positions. Then the third background should be of cleaner photos etc.

We will send you all the tabs and all the content later.

```html
<!DOCTYPE html>
<html lang="en">
<head>
<meta charset="utf-8">
<title>Lumara Maid Service</title>
<link rel="stylesheet" href="https://fonts.googleapis.com/css2?family=Bebas+Neue&family=Open+Sans:wght@400&family=Oxygen:wght@400&display=swap">
<style>
  :root {
    --yellow: #fff673;
    --gold: #c9a24a;
    --black: #000000;
    --white: #ffffff;
    --ink: #1a1a1a;
    --dot-grey: #d9d9d9;
  }
  * { margin: 0; padding: 0; box-sizing: border-box; }
  html, body { width: 1200px; height: 800px; overflow: hidden; background: var(--white); }
  body { position: relative; font-family: "Open Sans", sans-serif; color: var(--ink); }

  .site-header { position: absolute; left: 0; top: 0; width: 1200px; height: 100px; background: var(--white); }
  .brand { position: absolute; left: 100px; top: 40px; display: flex; align-items: center; gap: 10px; }
  .brand-mark { width: 18px; height: 18px; border-radius: 50%; background: var(--gold); }
  .brand-name { font-family: "Open Sans", sans-serif; font-size: 17px; font-weight: 400; color: var(--gold); }

  .main-nav { position: absolute; left: 524px; top: 33px; display: flex; gap: 16px; list-style: none; }
  .main-nav a { display: block; height: 42px; line-height: 42px; padding: 0 20px; font-size: 14px; color: var(--ink); text-decoration: none; border-radius: 4px; }
  .main-nav a.is-active { background: var(--yellow); }

  .hero { position: absolute; left: 0; top: 100px; width: 1200px; height: 600px; }
  .hero-photo { position: absolute; inset: 0; background: linear-gradient(100deg, #b89a5e 0%, #e2c98a 30%, #8a6f48 55%, #2a2730 75%, #d9c39a 100%); }
  .hero-content { position: absolute; left: 100px; top: 184px; width: 530px; }
  .hero-title { font-family: "Bebas Neue", sans-serif; font-weight: 400; font-size: 48px; line-height: 56px; color: var(--yellow); }
  .hero-text { margin-top: 8px; font-size: 17px; line-height: 30px; color: var(--white); }
  .hero-button { display: inline-block; margin-top: 24px; width: 134px; height: 54px; line-height: 56px; text-align: center; background: var(--yellow); color: var(--black); font-family: "Bebas Neue", sans-serif; font-size: 23px; text-decoration: none; }
  .hero-arrow { position: absolute; top: 290px; width: 26px; height: 40px; }
  .hero-arrow.prev { left: 42px; }
  .hero-arrow.next { left: 1131px; }
  .hero-dots { position: absolute; left: 1026px; top: 575px; display: flex; gap: 8px; }
  .hero-dots span { width: 13px; height: 13px; border-radius: 50%; background: var(--white); border: 1px solid #555; }
  .hero-dots span.is-active { background: var(--yellow); }

  .site-footer { position: absolute; left: 0; top: 700px; width: 1200px; height: 100px; background: var(--black); color: var(--white); font-family: "Oxygen", sans-serif; }
  .footer-nav { position: absolute; left: 98px; top: 23px; font-size: 17px; }
  .footer-nav a { color: var(--white); text-decoration: none; }
  .footer-nav .sep { margin: 0 9px; }
  .copyright { position: absolute; left: 98px; top: 58px; font-size: 13px; }
  .social { position: absolute; left: 978px; top: 38px; display: flex; gap: 8px; }
  .social span { width: 24px; height: 24px; border-radius: 3px; }
  .social .s1 { background: #3b5a9a; }
  .social .s2 { background: #48b0e0; }
  .social .s3 { background: #1f7bb6; }
  .social .s4 { background: #f28a1c; }
</style>
</head>
<body>
  <header class="site-header">
    <div class="brand"><span class="brand-mark"></span><span class="brand-name">Lumara Maid Service</span></div>
    <ul class="main-nav">
      <li><a class="is-active" href="#">Home</a></li>
      <li><a href="#">About Us</a></li>
      <li><a href="#">Services</a></li>
      <li><a href="#">Testimonals</a></li>
      <li><a href="#">Contact Us</a></li>
    </ul>
  </header>

  <section class="hero">
    <div class="hero-photo" role="img" aria-label="Photo of a cleaner in a dark uniform and yellow gloves wiping a skirting board in a bright room"></div>
    <svg class="hero-arrow prev" viewBox="0 0 26 40"><polyline points="20,4 6,20 20,36" fill="none" stroke="#fff" stroke-width="7" stroke-linejoin="miter"/></svg>
    <svg class="hero-arrow next" viewBox="0 0 26 40"><polyline points="6,4 20,20 6,36" fill="none" stroke="#fff" stroke-width="7" stroke-linejoin="miter"/></svg>
    <div class="hero-content">
      <h1 class="hero-title">LOREM IPSUM DOLOR SIT AMET</h1>
      <p class="hero-text">Nulla consequat massa quis enim. Donec pede justo, fringilla vel, aliquet nec, vulputate eget, arcu. In enim justo, rhoncus ut, imperdiet a, venenatis vitae, justo.</p>
      <a class="hero-button" href="#">READ MORE +</a>
    </div>
    <div class="hero-dots"><span></span><span class="is-active"></span><span></span></div>
  </section>

  <footer class="site-footer">
    <nav class="footer-nav">
      <a href="#">Home</a><span class="sep">|</span><a href="#">About Us</a><span class="sep">|</span><a href="#">Services</a><span class="sep">|</span><a href="#">Products</a><span class="sep">|</span><a href="#">Contact Us</a><span class="sep">|</span><a href="#">Blog</a>
    </nav>
    <p class="copyright">© 2014 Company Name&nbsp; All right reserved&nbsp; Term of Use</p>
    <div class="social"><span class="s1"></span><span class="s2"></span><span class="s3"></span><span class="s4"></span></div>
  </footer>
</body>
</html>
```